Business card for Eyelash extension salon in Beverly Hills,California USA

We need new business card for our salon in Beverly Hills. The salon name is 'Lashvera' . We would like to have...Business name: Lashvera Name of person: will provide later Address 4720 N.Alder Crest Ave Beverly Hills , CA 90210 Phone: will provide later (Text only) Web: www.lashverastudio.example Snapgrid icon, Circlebook icon follow us for seasonal campaign and news @lashverastudiolounge Design should look elegant, high-end, clean, simple, cohesive with my brand. Please refer my brand board. Business name color will be metallic bronzy color. Im thinking grey background or white background. Thanks

Target Market(s)

25-35. Gender neutral. People who are in Entertainment business industry.
This is High-end Eyelash extension salon in Beverly Hills

Industry/Entity Type

Beauty Salon

Contact Information for Business Card

Business name: Lashvera
Name of person: will provide later
Address 4720 N.Alder Crest Ave Beverly Hills , CA 90210
Phone: will provide later (Text only)
Web: www.lashverastudio.example
Snapgrid icon, Circlebook icon
follow us for seasonal campaign and news @lashverastudiolounge

Requirements
Must have
• Beautiful, elegant, clean and simple look but very attractive and modern
Should not have
• We don't like too clutter, too busy designs.

```html
<!DOCTYPE html>
<html lang="en">
<head>
<meta charset="utf-8">
<title>Lashvera Business Card</title>
<link rel="stylesheet" href="https://fonts.googleapis.com/css2?family=Playfair+Display:wght@600&family=Cormorant+Garamond:wght@500&family=Crimson+Text&family=Josefin+Sans:wght@400&display=swap">
<style>
  :root {
    --backdrop: #2b2b2b;
    --bronze: #8a6448;
    --ink: #3f3f3f;
    --muted: #a7a7a7;
    --card-light: #fbfbfb;
    --card-shade: #d9d9d9;
    --rule: #b9b9b9;
    --white: #ffffff;
  }
  * { margin: 0; padding: 0; box-sizing: border-box; }
  html, body { width: 1200px; height: 960px; overflow: hidden; }
  body { background: var(--backdrop); position: relative; font-family: "Crimson Text", serif; }

  .card { position: absolute; width: 600px; height: 343px; overflow: hidden; }

  /* Front */
  .card-front {
    left: 302px; top: 122px;
    background: radial-gradient(ellipse 70% 90% at 60% 35%, var(--card-light) 0%, #efefef 55%, var(--card-shade) 100%);
  }
  .brand-name {
    position: absolute; left: 40px; top: 128px; width: 260px; text-align: center;
    font-family: "Cormorant Garamond", serif; font-weight: 500; font-size: 62px;
    color: var(--bronze); letter-spacing: 1px; line-height: 1;
  }
  .divider { position: absolute; left: 311px; top: 80px; width: 1px; height: 185px; background: var(--rule); }
  .contact-block { position: absolute; left: 338px; top: 84px; color: var(--ink); }
  .person-name {
    font-family: "Playfair Display", serif; font-weight: 600; font-size: 21px;
    color: var(--bronze); letter-spacing: 0.5px; line-height: 1.1;
  }
  .person-title { font-family: "Crimson Text", serif; font-size: 15px; color: var(--muted); letter-spacing: 0.5px; line-height: 1.1; }
  .address { margin-top: 12px; font-size: 15px; line-height: 18px; }
  .contact-list { margin-top: 12px; list-style: none; font-size: 15px; }
  .contact-list li { display: flex; align-items: center; gap: 8px; line-height: 19px; }
  .contact-list svg { width: 13px; height: 13px; fill: var(--ink); flex: none; }
  .front-rule { position: absolute; left: 0; right: 0; top: 323px; height: 2px; background: var(--rule); }
  .front-band { position: absolute; left: 0; right: 0; bottom: 0; height: 15px; background: var(--bronze); }

  /* Back */
  .card-back { left: 299px; top: 495px; }
  .interior-photo {
    position: absolute; inset: 0;
    background: linear-gradient(100deg, #d2d2d0 0%, #ecebe8 22%, #f4f3f1 50%, #e9e7e3 75%, #d8d6d3 100%);
  }
  .back-brand {
    position: absolute; left: 0; right: 0; top: 118px; text-align: center;
    font-family: "Cormorant Garamond", serif; font-weight: 500; font-size: 86px;
    color: var(--bronze); letter-spacing: 1px; line-height: 1;
  }
  .social-list { position: absolute; right: 34px; top: 36px; display: flex; gap: 10px; list-style: none; }
  .social-list li {
    font-family: "Crimson Text", serif; font-size: 12px; color: var(--bronze);
    display: flex; align-items: center; gap: 4px;
  }
  .social-list .dot { width: 7px; height: 7px; border-radius: 50%; background: var(--bronze); }
  .web-band {
    position: absolute; left: 0; right: 0; top: 286px; height: 23px; background: var(--bronze);
    color: var(--white); text-align: center; font-family: "Crimson Text", serif;
    font-size: 15px; letter-spacing: 3.2px; line-height: 23px;
  }
</style>
</head>
<body>

<section class="card card-front" aria-label="Business card front">
  <div class="brand-name">Lashvera</div>
  <div class="divider"></div>
  <div class="contact-block">
    <h1 class="person-name">MARA ELLISON</h1>
    <p class="person-title">CEO/FOUNDER</p>
    <p class="address">4720 N.Alder Crest<br>Ave Beverly Hills<br>CA 90210</p>
    <ul class="contact-list">
      <li>
        <svg viewBox="0 0 24 24" aria-hidden="true"><path d="M6.6 10.8a15.1 15.1 0 0 0 6.6 6.6l2.2-2.2c.3-.3.7-.4 1-.2 1.1.4 2.3.6 3.6.6.6 0 1 .4 1 1V20c0 .6-.4 1-1 1A17 17 0 0 1 3 4c0-.6.4-1 1-1h3.5c.6 0 1 .4 1 1 0 1.3.2 2.5.6 3.6.1.3 0 .7-.2 1z"/></svg>
        310 555 0148
      </li>
      <li>
        <svg viewBox="0 0 24 24" aria-hidden="true"><path d="M2 5h20v14H2zM4 7v.5l8 5 8-5V7l-8 5z"/></svg>
        news@lashverastudio.example
      </li>
      <li>
        <svg viewBox="0 0 24 24" aria-hidden="true"><path d="M12 2a10 10 0 1 0 0 20 10 10 0 0 0 0-20zm-1 17.9A8 8 0 0 1 4.2 10L9 14.8v1a2 2 0 0 0 2 2zm6.9-2.5a2 2 0 0 0-1.9-1.4h-1v-3a1 1 0 0 0-1-1H8v-2h2a1 1 0 0 0 1-1V7h2a2 2 0 0 0 2-2v-.4a8 8 0 0 1 2.9 12.8z"/></svg>
        www.lashverastudio.example
      </li>
    </ul>
  </div>
  <div class="front-rule"></div>
  <div class="front-band"></div>
</section>

<section class="card card-back" aria-label="Business card back">
  <div class="interior-photo" role="img" aria-label="Soft, bright photograph of a white salon lounge interior with windows, armchairs and a wooden table"></div>
  <ul class="social-list">
    <li><span class="dot"></span>Circlebook</li>
    <li><span class="dot"></span>Snapgrid</li>
  </ul>
  <div class="back-brand">Lashvera</div>
  <div class="web-band">www.lashverastudio.example</div>
</section>

</body>
</html>
```